Upscale business cards needed for Board of Directors

We need professional business cards created for members of our family business Board of Directors. We would like these relatively simple and straightforward, but also with a unique element to set them apart. Probably stick with neutral and simple colors - white, grey etc. We need space for the traditional elements, including name, title, address, email/phone number. And we will be creating several from this template so it needs to be template that is easy to switch information in and out of.
Business
See description

```html
<!DOCTYPE html>
<html lang="en">
<head>
<meta charset="utf-8">
<title>Harborline Holdings – Business Cards</title>
<link rel="stylesheet" href="https://fonts.googleapis.com/css2?family=Source+Sans+3:wght@400;600&display=swap">
<style>
  :root {
    --backdrop: #ece9e4;
    --card-dark: #231f20;
    --card-gold: #b39f73;
    --text-light: #ffffff;
    --logo-light: #e2e3e1;
    --logo-dark: #231f20;
    --font-main: "Source Sans 3", "Myriad Pro", Arial, sans-serif;
  }
  * { margin: 0; padding: 0; box-sizing: border-box; }
  html, body {
    width: 1200px;
    height: 900px;
    overflow: hidden;
  }
  body {
    position: relative;
    background: var(--backdrop);
    font-family: var(--font-main);
  }
  .card {
    position: absolute;
    width: 556px;
    height: 342px;
    box-shadow: 0 6px 18px rgba(0, 0, 0, 0.18);
  }
  .card--front {
    left: 238px;
    top: 62px;
    background: var(--card-dark);
    color: var(--text-light);
  }
  .card--back {
    left: 458px;
    top: 518px;
    background: var(--card-gold);
  }
  .brand-name {
    position: absolute;
    font-family: var(--font-main);
    font-weight: 600;
    font-size: 34px;
    letter-spacing: 3px;
    line-height: 1;
    text-transform: uppercase;
    white-space: nowrap;
  }
  .card--front .brand-name {
    right: 40px;
    top: 72px;
    color: var(--logo-light);
  }
  .card--back .brand-name {
    left: 0;
    right: 0;
    top: 152px;
    text-align: center;
    color: var(--logo-dark);
  }
  .contact-block {
    position: absolute;
    left: 33px;
    top: 134px;
  }
  .person-name {
    font-size: 23px;
    font-weight: 400;
    line-height: 1.1;
  }
  .person-title {
    font-size: 15px;
    line-height: 1.3;
    margin-top: 2px;
  }
  .address {
    font-size: 15px;
    line-height: 20px;
    margin-top: 14px;
    font-style: normal;
  }
  .contact-list {
    list-style: none;
    margin-top: 12px;
    font-size: 15px;
    line-height: 20px;
  }
  .contact-list li {
    display: flex;
    align-items: center;
    gap: 8px;
  }
  .contact-icon {
    width: 12px;
    height: 12px;
    flex: none;
  }
</style>
</head>
<body>

  <section class="card card--front" aria-label="Business card front">
    <div class="brand-name">Harborline Holdings</div>

    <div class="contact-block">
      <h1 class="person-name">Daniel Carter</h1>
      <p class="person-title">Managing Director</p>
      <address class="address">2780, Harbor View Road<br>Westmere Bay, 550123.</address>
      <ul class="contact-list">
        <li>
          <svg class="contact-icon" viewBox="0 0 12 12" aria-hidden="true">
            <path d="M2.3 1 L4.2 1 L5 3.4 L3.8 4.4 Q4.8 6.9 7.6 8.2 L8.6 7 L11 7.8 L11 9.7 Q10.5 11 9 11 Q1 10 1 2.6 Q1 1 2.3 1 Z" fill="#fff"/>
          </svg>
          044-555 010 234
        </li>
        <li>
          <svg class="contact-icon" viewBox="0 0 12 12" aria-hidden="true">
            <rect x="1" y="2.5" width="10" height="7" fill="#fff"/>
            <path d="M1 2.5 L6 6.5 L11 2.5" fill="none" stroke="#231f20" stroke-width="1"/>
          </svg>
          info@harborline-mail.com
        </li>
        <li>
          <svg class="contact-icon" viewBox="0 0 12 12" aria-hidden="true">
            <g fill="none" stroke="#fff" stroke-width="1.3" stroke-linecap="round">
              <path d="M5 7 L7 5"/>
              <path d="M6.2 3.2 L7.4 2 Q8.6 0.8 9.8 2 Q11 3.2 9.8 4.4 L8.6 5.6"/>
              <path d="M5.8 8.8 L4.6 10 Q3.4 11.2 2.2 10 Q1 8.8 2.2 7.6 L3.4 6.4"/>
            </g>
          </svg>
          www.harborline-group.com
        </li>
      </ul>
    </div>
  </section>

  <section class="card card--back" aria-label="Business card back">
    <div class="brand-name">Harborline Holdings</div>
  </section>

</body>
</html>
```